Animal Eye Clinic needs a Business card

We are a new veterinary ophthalmology practice (Ridgeline Pet Vision Care) and we need a business card designed. We only see animal eyes - we are not a regular veterinary clinic. We already have a logo. We are looking for a professional, good looking business card to hand out to our clients. We are looking for something simple but professional and contemporary. Our logo is likely the only picture/graphic that needs to be on the card.
Updates

Contact Information for Business Card

Delia Vossman, BSc, DVM, MSc, DipACVO
Veterinary Ophthalmologist

Phone: 250.418.3927
Email: ridgelinepetvisioncare@mailbox-example.net
Website: ridgelinepetvisioncare-example.net
Address: 1874 Thornbury Rd
Kelowna, BC, V1X 4M9

Colors

Designer to choose colors to be used in the design.

Requirements
Must have
• Our logo (attached)

```html
<!DOCTYPE html>
<html lang="en">
<head>
<meta charset="utf-8">
<title>Ridgeline Pet Vision Care — Business Card</title>
<link href="https://fonts.googleapis.com/css2?family=Roboto:wght@300;400;500;700&display=swap" rel="stylesheet">
<style>
  :root {
    --page-bg: #e6e4e1;
    --card-bg: #2f3032;
    --card-bg-deep: #262729;
    --pattern-light: #4a4c4f;
    --teal: #1a9aaa;
    --text-light: #e9eaeb;
    --rule: #9a9c9f;
  }
  * { box-sizing: border-box; margin: 0; padding: 0; }
  html, body {
    width: 1200px; height: 716px; overflow: hidden;
    background: var(--page-bg);
    font-family: "Roboto", sans-serif;
  }
  .canvas {
    position: relative; width: 1200px; height: 716px;
    display: flex; align-items: center; justify-content: center; gap: 40px;
  }
  .card {
    position: relative; width: 540px; height: 309px;
    background: var(--card-bg);
    border-left: 3px solid var(--teal);
    border-bottom: 3px solid var(--teal);
    box-shadow: 0 8px 22px rgba(0,0,0,0.25);
    overflow: hidden;
  }

  /* Front */
  .card-front { background: var(--card-bg-deep); }
  .front-pattern {
    position: absolute; inset: 0;
    background: linear-gradient(120deg, var(--card-bg-deep) 0%, #303234 55%, var(--pattern-light) 100%);
  }
  .front-brand {
    position: absolute; left: 190px; top: 170px;
    display: flex; align-items: center; gap: 12px;
  }

  /* Shared brand lockup */
  .brand-dot {
    width: 34px; height: 34px; border-radius: 50%;
    background: var(--teal); flex: none;
  }
  .brand-name {
    color: var(--teal); font-weight: 500; text-transform: uppercase;
    line-height: 1.1;
  }
  .brand-name .line-top { display: block; font-size: 11px; letter-spacing: 5px; }
  .brand-name .line-bottom { display: block; font-size: 17px; letter-spacing: 0.5px; }

  /* Back */
  .back-brand {
    position: absolute; right: 30px; top: 72px;
    display: flex; align-items: center; gap: 12px;
  }
  .back-brand .brand-dot { width: 40px; height: 40px; }
  .back-brand .line-top { font-size: 12px; letter-spacing: 6px; }
  .back-brand .line-bottom { font-size: 19px; }

  .person { position: absolute; left: 32px; top: 112px; }
  .person-name { color: var(--teal); font-weight: 700; font-size: 13px; letter-spacing: 0.2px; }
  .person-title { color: var(--text-light); font-weight: 300; font-size: 12px; margin-top: 3px; }

  .divider {
    position: absolute; left: 32px; top: 156px; width: 400px; height: 1px;
    background: var(--rule);
  }

  .contact-list { position: absolute; left: 32px; top: 172px; list-style: none; }
  .contact-list li {
    display: flex; align-items: center; gap: 7px;
    color: var(--text-light); font-weight: 300; font-size: 11.5px; line-height: 18px;
  }
  .contact-list svg { width: 10px; height: 10px; fill: var(--teal); flex: none; }
  .contact-list .accent { color: var(--teal); }

  .address {
    position: absolute; right: 40px; bottom: 30px;
    color: var(--text-light); font-weight: 300; font-size: 12.5px; line-height: 17px;
  }
</style>
</head>
<body>
<main class="canvas">

  <section class="card card-front" aria-label="Card front">
    <div class="front-pattern" role="img" aria-label="Tonal repeating pattern of the clinic's eye mark"></div>
    <div class="front-brand">
      <span class="brand-dot"></span>
      <span class="brand-name"><span class="line-top">Ridgeline</span><span class="line-bottom">Pet Vision Care</span></span>
    </div>
  </section>

  <section class="card card-back" aria-label="Card back">
    <div class="back-brand">
      <span class="brand-dot"></span>
      <span class="brand-name"><span class="line-top">Ridgeline</span><span class="line-bottom">Pet Vision Care</span></span>
    </div>

    <div class="person">
      <p class="person-name">Delia Vossman, BSc, DVM, MSc, DipACVO</p>
      <p class="person-title">Veterinary Ophthalmologist</p>
    </div>

    <div class="divider"></div>

    <ul class="contact-list">
      <li>
        <svg viewBox="0 0 24 24" aria-hidden="true"><path d="M6.6 10.8a15.1 15.1 0 0 0 6.6 6.6l2.2-2.2a1 1 0 0 1 1-.25 11.4 11.4 0 0 0 3.6.57 1 1 0 0 1 1 1V20a1 1 0 0 1-1 1A17 17 0 0 1 3 4a1 1 0 0 1 1-1h3.5a1 1 0 0 1 1 1c0 1.25.2 2.45.57 3.57a1 1 0 0 1-.25 1z"/></svg>
        250.418.3927
      </li>
      <li>
        <svg viewBox="0 0 24 24" aria-hidden="true"><path d="M2 5h20v14H2zm2 2v.5l8 5 8-5V7l-8 5z"/></svg>
        ridgelinepetvisioncare@mailbox-example.net
      </li>
      <li>
        <svg viewBox="0 0 24 24" aria-hidden="true"><circle cx="12" cy="12" r="10"/></svg>
        <span>www.<span class="accent">ridgelinepetvisioncare-example</span>.net</span>
      </li>
    </ul>

    <address class="address">
      1874 Thornbury Rd<br>
      Kelowna, BC, V1X 4M9
    </address>
  </section>

</main>
</body>
</html>
```